Vortel surface design based website for technology jobs website

We need a website design for a technology job listing website, mainly aiming at 20/30/40 year old nerds. Jobs listed from multiple sources will be concatenated and organised. This website will be built with Vortel surface design (https://surfacekit.example/guidelines/) so please use their components. The design should be simple and clear, so a user can directly look for offerings that are interesting for him.

Three different pages will be needed:

1. Main jobs list page

Contains a large table (https://surfacekit.example/guidelines/components/data-tables.html#data-tables-structure), on top or next to this data-table users should be able to apply filters (select countries, select salary ranges) and somewhere an overview of the selected filters should be shown.

- A subscribe bar should be shown somewhere to allow a user to register for weekly/monthly mailings for new job offers with his preferred search filters.

2. Selected item page

If an item is clicked, a user should be able to view a job posting and it's details.

3. An advertiser should be able post his job offer.
Similar fields as https://post.ledgerworkboard.example/.
(https://surfacekit.example/guidelines/components/text-fields.html#text-fields-layout)

Target Market(s)

20/30/40 year old nerds.

Industry/Entity Type

Computer

Logo Text

TechHirePlaza.example

Number of Pages Required

3 page

Colors

Designer to choose colors to be used in the design.

Requirements
Must have
• 1. Main jobs list page
• Contains a large table (https://surfacekit.example/guidelines/components/data-tables.html#data-tables-structure), on top or next to this data-table users should be able to apply filters (select countries, select salary ranges) and somewhere an overview of the selected filters should be shown.
• - A subscribe bar should be shown somewhere to allow a user to register for weekly/monthly mailings for new job offers with his preferred search filters.
• 2. Selected item page
• If an item is clicked, a user should be able to view a job posting and it's details.
• 3. An advertiser should be able post his job offer,
• (https://surfacekit.example/guidelines/components/text-fields.html#text-fields-layout)
• Please use open fonts!

```html
<!DOCTYPE html>
<html lang="en">
<head>
<meta charset="utf-8">
<title>Veldmark – Technology Jobs</title>
<link href="https://fonts.googleapis.com/css2?family=Open+Sans:wght@400;600;700;800&display=swap" rel="stylesheet">
<style>
:root{
  --ink:#2b2f36;
  --muted:#7a7f87;
  --orange:#f7a21b;
  --orange-dark:#e58e0c;
  --green:#2f9e2f;
  --blue-link:#2a6fc9;
  --band:#1f64b5;
  --band-dark:#164c8f;
  --grey-bg:#eeeff1;
  --line:#dcdee2;
  --white:#ffffff;
  --header-dark:#26292e;
}
*{box-sizing:border-box;margin:0;padding:0}
html,body{width:755px;height:1200px;overflow:hidden}
body{font-family:"Open Sans",Arial,sans-serif;color:var(--ink);background:var(--white);position:relative}

/* Hero */
.hero{position:absolute;left:0;top:0;width:755px;height:375px;overflow:hidden}
.hero-photo{position:absolute;inset:0;background:linear-gradient(110deg,#3c4451 0%,#6d7886 35%,#8e97a2 55%,#4b5360 80%,#2d333c 100%)}
.hero-shade{position:absolute;inset:0;background:rgba(20,24,30,.35)}
.brand{position:absolute;left:0;top:0;width:205px;height:46px;background:var(--header-dark);
  clip-path:polygon(0 0,100% 0,88% 100%,0 100%);display:flex;align-items:center;padding-left:18px}
.brand-name{color:var(--white);font-weight:800;font-size:19px;letter-spacing:.5px}
.main-nav{position:absolute;right:0;top:0;left:210px;height:40px;background:var(--white);
  display:flex;justify-content:flex-end;align-items:center;padding-right:16px;gap:4px}
.main-nav a{font-size:8px;font-weight:700;color:#444;text-decoration:none;padding:6px 8px;letter-spacing:.3px}
.main-nav a.active{color:var(--orange);border-bottom:2px solid var(--orange)}
.hero-title{position:absolute;left:0;right:0;top:170px;text-align:center;color:var(--white);
  font-size:26px;font-weight:800;line-height:1.25;letter-spacing:.5px}
.btn{display:inline-block;border:none;font-family:inherit;font-weight:700;color:var(--white);text-align:center}
.btn-orange{background:var(--orange)}
.hero-cta{position:absolute;left:332px;top:240px;width:92px;height:24px;line-height:24px;font-size:8px;border-radius:2px}

/* Welcome */
.welcome{position:absolute;left:48px;top:408px;width:420px}
.welcome h2{font-size:17px;font-weight:700;margin-bottom:10px}
.welcome p{font-size:8.5px;line-height:1.6;color:var(--muted)}
.read-more{margin-top:14px;width:76px;height:24px;line-height:24px;font-size:8px;border-radius:12px}
.testimonials{position:absolute;left:493px;top:408px;width:212px;height:118px;background:var(--grey-bg);border-radius:6px;padding:10px 14px}
.testimonials h3{font-size:14px;font-weight:600;margin-bottom:8px}
.testimonials .arrows{position:absolute;right:12px;top:12px;display:flex;gap:8px}
.testimonials blockquote{font-size:7.5px;line-height:1.6;color:var(--muted);background:var(--white);border-radius:4px;padding:8px}
.testimonials cite{display:block;font-style:normal;font-weight:700;color:var(--blue-link);margin-top:2px}

/* Jobs */
.jobs-head{position:absolute;left:48px;top:600px;width:660px;height:30px;display:flex;align-items:center}
.jobs-head h2{font-size:17px;font-weight:700;flex:1}
.filter-link{font-size:7.5px;font-weight:700;color:var(--blue-link);margin-right:14px;display:flex;align-items:center;gap:4px}
.select{width:100px;height:22px;border:1px solid var(--line);border-radius:3px;font-size:7.5px;color:var(--muted);
  display:flex;align-items:center;justify-content:space-between;padding:0 8px;margin-right:10px;background:var(--white)}
.apply-btn{width:50px;height:22px;line-height:22px;font-size:8px;border-radius:11px}
.jobs-table{position:absolute;left:48px;top:642px;width:660px;border-collapse:collapse;font-size:7.5px;
  box-shadow:0 2px 6px rgba(0,0,0,.12)}
.jobs-table th{background:#e3e5e8;height:32px;text-align:left;font-weight:700;font-size:7.5px;padding:0 10px;color:#333}
.jobs-table td{height:35px;padding:0 10px;border-top:1px solid var(--line);color:#555}
.jobs-table tbody tr:nth-child(even) td{background:#f7f8f9}
.job-name{color:var(--blue-link);font-weight:700}
.apply-now{width:64px;height:20px;line-height:20px;font-size:7px;border-radius:10px;background:var(--green)}

/* Subscribe */
.subscribe{position:absolute;left:0;top:947px;width:755px;height:130px;background:linear-gradient(120deg,var(--band-dark),var(--band) 60%,#2a78cc);text-align:center;color:var(--white)}
.subscribe h2{font-size:17px;font-weight:600;margin-top:24px}
.subscribe p{font-size:8px;opacity:.85;margin-top:6px}
.subscribe-form{display:flex;justify-content:center;margin-top:12px}
.email-input{width:212px;height:26px;background:var(--white);border-radius:13px 0 0 13px;color:var(--muted);font-size:8px;text-align:left;padding-left:14px;line-height:26px}
.signup{width:56px;height:26px;line-height:26px;font-size:8px;border-radius:0 13px 13px 0}

/* Footer */
.site-footer{position:absolute;left:0;top:1077px;width:755px;height:123px;text-align:center}
.site-footer p{font-size:7.5px;color:var(--muted);margin-top:46px}
.social{display:flex;justify-content:center;gap:12px;margin-top:8px}
.social span{width:12px;height:12px;background:var(--ink);border-radius:2px}
</style>
</head>
<body>

<section class="hero">
  <div class="hero-photo" role="img" aria-label="Photo of a professional working at a laptop in an office"></div>
  <div class="hero-shade"></div>
  <div class="brand"><span class="brand-name">VELDMARK</span></div>
  <nav class="main-nav">
    <a class="active">HOME</a><a>ABOUT US</a><a>SERVICES</a><a>JOBS</a><a>NEWS</a><a>BLOG</a><a>SUPPORT</a><a>CONTACT US</a>
  </nav>
  <h1 class="hero-title">SEARCH YOUR FAVOURITE PROFESSIONAL<br>WITH VELDMARK</h1>
  <span class="btn btn-orange hero-cta">GET STARTED</span>
</section>

<section class="welcome">
  <h2>Welcome to Our Website</h2>
  <p>Aliquam molestie, mi et imperdiet euismod, dui purus auctor tellus, et interdum lacus lectus et ante. Sed accumsan sollicitudin turpis, sit amet adipiscing turpis porttitor in. In congue, neque ut lobortis volutpat, libero mauris varius mi, vitae suscipit ipsum ligula vitae risus. Donec aliquam nibh a dui iaculis.</p>
  <span class="btn btn-orange read-more">READ MORE</span>
</section>

<aside class="testimonials">
  <h3>Testimonials</h3>
  <div class="arrows">
    <svg width="6" height="9" viewBox="0 0 6 9"><path d="M5 1 1 4.5 5 8" fill="none" stroke="#555" stroke-width="1.5"/></svg>
    <svg width="6" height="9" viewBox="0 0 6 9"><path d="M1 1 5 4.5 1 8" fill="none" stroke="#555" stroke-width="1.5"/></svg>
  </div>
  <blockquote>“Aliquam molestie, mi et imperdiet euismod, dui purus auctor tellus, et interdum lacus lectus et ante.”
    <cite>- Name Heading</cite></blockquote>
</aside>

<div class="jobs-head">
  <h2>Featured Jobs Listing</h2>
  <span class="filter-link">
    <svg width="8" height="8" viewBox="0 0 8 8"><path d="M0 0h8L5 4v4L3 7V4z" fill="#2a6fc9"/></svg>APPLY FILTER</span>
  <span class="select">Select Country
    <svg width="6" height="4" viewBox="0 0 6 4"><path d="M0 0h6L3 4z" fill="#888"/></svg></span>
  <span class="select">Select Salary
    <svg width="6" height="4" viewBox="0 0 6 4"><path d="M0 0h6L3 4z" fill="#888"/></svg></span>
  <span class="btn btn-orange apply-btn">APPLY</span>
</div>

<table class="jobs-table">
  <thead><tr><th>S.NO</th><th>JOB NAME</th><th>JOB POSITION</th><th>LOCATION</th><th>JOB TYPE</th><th>EXP</th><th>ACTION</th></tr></thead>
  <tbody>
    <tr><td>1.</td><td class="job-name">LOREM IPSUM DOLOR</td><td>Consectetuer</td><td>Mamoru Road,Glasgow</td><td>Full Time</td><td>3yrs</td><td><span class="btn apply-now">APPLY NOW</span></td></tr>
    <tr><td>2.</td><td class="job-name">LOREM IPSUM DOLOR</td><td>Consectetuer</td><td>Mamoru Road,Glasgow</td><td>Part Time</td><td>8yrs</td><td><span class="btn apply-now">APPLY NOW</span></td></tr>
    <tr><td>3.</td><td class="job-name">LOREM IPSUM DOLOR</td><td>Consectetuer</td><td>Mamoru Road,Glasgow</td><td>Full Time</td><td>2yrs</td><td><span class="btn apply-now">APPLY NOW</span></td></tr>
    <tr><td>4.</td><td class="job-name">LOREM IPSUM DOLOR</td><td>Consectetuer</td><td>Mamoru Road,Glasgow</td><td>Part Time</td><td>5yrs</td><td><span class="btn apply-now">APPLY NOW</span></td></tr>
    <tr><td>5.</td><td class="job-name">LOREM IPSUM DOLOR</td><td>Consectetuer</td><td>Mamoru Road,Glasgow</td><td>Full Time</td><td>3yrs</td><td><span class="btn apply-now">APPLY NOW</span></td></tr>
    <tr><td>6.</td><td class="job-name">LOREM IPSUM DOLOR</td><td>Consectetuer</td><td>Mamoru Road,Glasgow</td><td>Part Time</td><td>4yrs</td><td><span class="btn apply-now">APPLY NOW</span></td></tr>
  </tbody>
</table>

<section class="subscribe">
  <h2>Weekly Email Subscribe</h2>
  <p>Subscribe for weekly/monthly mailings for new job offers.</p>
  <div class="subscribe-form">
    <span class="email-input">Enter Email Address</span>
    <span class="btn btn-orange signup">Sign Up</span>
  </div>
</section>

<footer class="site-footer">
  <p>Copyright © 2018 Company Name. All Rights Reserved, Privacy Policy</p>
  <div class="social"><span></span><span></span><span></span><span></span><span></span></div>
</footer>

</body>
</html>
```